Home Remodeling company needs a business card design

we need a business card design for home remodeling company in hamilton county, indiana USA. we offers a wide range of construction services including whole house renovations, Design and Build Basements and Kitchen and Bathroom Remodeling . we would like to see designs for both site of business card that use the same color of the company logo and also including all information below :
1- Karim Feltous CEO / General Contractor
2- all company contacts Telephone numbers ( 1-888-DULOM-47 ) ( 317-555-0193) email address ( info@dulomhome.com) website ( www.dulomhome.com ) and social media logos (Facebook- twitter- google plus )
3- company logo
4- licensed . insured . bonded

```html
<!DOCTYPE html>
<html lang="en">
<head>
<meta charset="utf-8">
<title>Dulom Home Remodeling – Business Card</title>
<link rel="stylesheet" href="https://fonts.googleapis.com/css2?family=Ubuntu:wght@400;500;700&display=swap">
<style>
  :root {
    --stage: #e4e4e4;
    --ink-black: #000000;
    --paper-white: #ffffff;
    --brand-red: #c8323a;
    --brand-grey: #3a3a3a;
    --tag-grey: #5e5e5e;
    --muted-grey: #8a8a8a;
    --rule-grey: #3c3c3c;
  }
  * { box-sizing: border-box; margin: 0; padding: 0; }
  html, body {
    width: 1189px; height: 1200px; overflow: hidden;
    background: var(--stage);
    font-family: "Ubuntu", sans-serif;
  }
  .canvas { position: relative; width: 1189px; height: 1200px; }

  .card {
    position: absolute; left: 140px; width: 918px; height: 524px;
    overflow: hidden; background: var(--ink-black);
  }
  .card--front { top: 45px; }
  .card--back { top: 623px; }

  .front-shape { position: absolute; inset: 0; }

  .wordmark {
    position: absolute; display: flex; align-items: center;
    font-weight: 700; color: var(--brand-grey); line-height: 1;
  }
  .wordmark__square { display: block; background: var(--brand-red); }
  .card--front .wordmark { left: 161px; top: 40px; gap: 18px; font-size: 112px; letter-spacing: 22px; }
  .card--front .wordmark__square { width: 26px; height: 26px; }
  .card--back .wordmark { left: 119px; top: 150px; gap: 20px; font-size: 128px; letter-spacing: 25px; }
  .card--back .wordmark__square { width: 26px; height: 26px; }

  .tagline {
    position: absolute; font-weight: 500; text-transform: uppercase; line-height: 1;
  }
  .card--front .tagline { left: 198px; top: 144px; font-size: 27px; letter-spacing: 16.6px; color: var(--tag-grey); }
  .card--back .tagline { left: 163px; top: 269px; font-size: 32px; letter-spacing: 19.5px; color: var(--muted-grey); }

  .social { position: absolute; left: 161px; top: 178px; display: flex; gap: 19px; }
  .social__badge { width: 30px; height: 30px; border-radius: 3px; background: var(--brand-grey); }
  .social__badge:first-child { background: var(--brand-red); }

  .credentials {
    position: absolute; left: 372px; top: 180px; font-size: 31px; color: var(--tag-grey); line-height: 1;
  }

  .person { position: absolute; left: 83px; top: 345px; color: var(--paper-white); }
  .person__name { font-size: 49px; color: var(--brand-red); line-height: 1; margin-bottom: 8px; }
  .person__role { font-size: 29px; line-height: 30px; }

  .divider { position: absolute; left: 466px; top: 320px; width: 3px; height: 158px; background: var(--paper-white); }

  .contacts { position: absolute; left: 530px; top: 333px; list-style: none; }
  .contacts__item { display: flex; align-items: center; height: 33.7px; color: var(--paper-white); font-size: 24.5px; }
  .contacts__icon { width: 14px; height: 14px; margin-right: 10px; flex: none; }

  .back-rule { position: absolute; left: 0; top: 442px; width: 100%; height: 5px; background: var(--rule-grey); }
  .back-band { position: absolute; left: 0; top: 454px; width: 100%; height: 70px; background: var(--brand-red); }
</style>
</head>
<body>
<main class="canvas">

  <section class="card card--front" aria-label="Business card front">
    <svg class="front-shape" width="918" height="524" viewBox="0 0 918 524" aria-hidden="true">
      <polygon points="0,0 918,0 918,221 810,279 108,279 0,221" fill="var(--paper-white)"/>
      <polygon points="49,231 104,252 810,252 874,231 816,263 98,263" fill="var(--brand-red)"/>
    </svg>

    <div class="wordmark"><span class="wordmark__square"></span><span>DULOM</span></div>
    <p class="tagline">Home Remodeling</p>

    <div class="social" aria-label="Social media">
      <span class="social__badge"></span>
      <span class="social__badge"></span>
      <span class="social__badge"></span>
    </div>
    <p class="credentials">licensed .insured . bonded</p>

    <div class="person">
      <p class="person__name">Karim Feltous</p>
      <p class="person__role">General Contractor</p>
      <p class="person__role">CEO</p>
    </div>

    <div class="divider"></div>

    <ul class="contacts">
      <li class="contacts__item">
        <svg class="contacts__icon" viewBox="0 0 14 14" aria-hidden="true"><rect width="14" height="14" fill="var(--brand-red)"/><path d="M4 3h2l1 2.5-1.2 1a5 5 0 0 0 2.7 2.7l1-1.2L12 9v2a1 1 0 0 1-1 1A8 8 0 0 1 3 4a1 1 0 0 1 1-1z" fill="var(--ink-black)"/></svg>
        1-888-DULOM-47
      </li>
      <li class="contacts__item">
        <svg class="contacts__icon" viewBox="0 0 14 14" aria-hidden="true"><rect width="14" height="14" fill="var(--brand-red)"/><rect x="3" y="6" width="8" height="5" fill="var(--ink-black)"/><rect x="2" y="3" width="10" height="2" fill="var(--ink-black)"/></svg>
        317-555-0193
      </li>
      <li class="contacts__item">
        <svg class="contacts__icon" viewBox="0 0 14 14" aria-hidden="true"><rect width="14" height="14" fill="var(--brand-red)"/><rect x="2.5" y="4" width="9" height="6" fill="none" stroke="var(--ink-black)" stroke-width="1.2"/><path d="M2.5 4 7 7.5 11.5 4" fill="none" stroke="var(--ink-black)" stroke-width="1.2"/></svg>
        info@dulomhome.com
      </li>
      <li class="contacts__item">
        <svg class="contacts__icon" viewBox="0 0 14 14" aria-hidden="true"><rect width="14" height="14" fill="var(--brand-red)"/><circle cx="7" cy="7" r="4" fill="none" stroke="var(--ink-black)" stroke-width="1.2"/><path d="M3 7h8M7 3v8" stroke="var(--ink-black)" stroke-width="1"/></svg>
        www.dulomhome.com
      </li>
    </ul>
  </section>

  <section class="card card--back" aria-label="Business card back">
    <div class="wordmark"><span class="wordmark__square"></span><span>DULOM</span></div>
    <p class="tagline">Home Remodeling</p>
    <div class="back-rule"></div>
    <div class="back-band"></div>
  </section>

</main>
</body>
</html>
```